Business Card Re-Design/Update

We'd like to update out business cards. I've included our current "Style guide" which has the colour scheme of the organisation in it. I've also included the branding files with logos etc in them.

I've also included a copy of one of our existing cards so that you can see how ugly/dated they look. I'd like a fresh modern corporate look.

Target Market(s)

These are for our clients, potential clients, industry contacts - like all business cards

Contact Information for Business Card

Name
Position
Company Address - Level 1, 47 Fernby Street, Carlow Qld 4072
Direct Phone
mobile
Email
Website -www.korvalit.com.au
Logo

Colors

Designer to choose colors to be used in the design.

Requirements
Must have
• Main Logo
• Cards will need to be editable to be able to personalize them for each new employee.
Nice to have
• The MapOut, ShipWell, KeepSteady would be okay to have if they can be sensibly and professionally added to the look without detracting from the main imagery.
• Maybe they could go on the back of the card? will leave this to your creative discretion as to whether/where they fit.
Should not have
• Should not have decorative or script fonts

```html
<!DOCTYPE html>
<html lang="en">
<head>
<meta charset="utf-8">
<title>korvalIT business card</title>
<link href="https://fonts.googleapis.com/css2?family=Work+Sans:wght@400;500;600&display=swap" rel="stylesheet">
<style>
  :root {
    --brand-red: #d0191f;
    --ink: #3a3a3c;
    --ink-soft: #555558;
    --card-white: #ffffff;
    --card-dark: #2f2f31;
    --logo-light: #c9c9cb;
    --backdrop: #1e1e20;
  }
  * { margin: 0; padding: 0; box-sizing: border-box; }
  html, body {
    width: 1200px; height: 900px; overflow: hidden;
    background: var(--backdrop);
    font-family: "Work Sans", Arial, sans-serif;
  }
  .canvas { position: relative; width: 1200px; height: 900px; }
  .card {
    position: absolute; left: 290px; width: 620px; height: 370px;
    overflow: hidden; border-radius: 4px;
    box-shadow: 0 10px 30px rgba(0,0,0,0.5);
  }
  .card-front { top: 50px; background: var(--card-white); }
  .card-back { top: 470px; background: var(--card-dark); }

  .brand { display: flex; align-items: center; gap: 12px; }
  .brand-square { width: 30px; height: 30px; background: var(--brand-red); }
  .brand-name { font-weight: 500; letter-spacing: -0.5px; }

  .card-front .brand { position: absolute; left: 40px; top: 36px; }
  .card-front .brand-name { font-size: 40px; color: var(--ink); line-height: 1; }

  .person { position: absolute; left: 40px; top: 104px; }
  .person-name { font-size: 30px; font-weight: 600; color: var(--brand-red); letter-spacing: 1px; line-height: 1.05; }
  .person-role { font-size: 15px; color: var(--ink-soft); margin-top: 4px; }

  .contact-list { position: absolute; left: 40px; top: 178px; list-style: none; font-size: 14px; color: var(--ink); line-height: 21px; }
  .contact-list li { display: flex; align-items: center; gap: 8px; }
  .contact-list svg { width: 11px; height: 11px; flex: none; }
  .contact-list .address { padding-left: 19px; }
  .web-highlight { color: var(--brand-red); }

  .feature-block {
    position: absolute; right: -40px; bottom: 28px;
    width: 250px; height: 220px; background: var(--brand-red);
  }

  .card-back .brand { position: absolute; left: 50%; top: 50%; transform: translate(-50%, -50%); gap: 18px; }
  .card-back .brand-square { width: 46px; height: 46px; }
  .card-back .brand-name { font-size: 64px; color: var(--logo-light); line-height: 1; }
</style>
</head>
<body>
<main class="canvas">
  <section class="card card-front" aria-label="Card front">
    <div class="brand">
      <span class="brand-square"></span>
      <span class="brand-name">korvalIT</span>
    </div>
    <div class="person">
      <h1 class="person-name">DANA WHITFIELD</h1>
      <p class="person-role">Business Development Manager</p>
    </div>
    <ul class="contact-list">
      <li class="address">Level 1, 47 Fernby Street,</li>
      <li class="address">Carlow QLD 4072</li>
      <li><svg viewBox="0 0 10 10"><rect x="2.5" y="0.5" width="5" height="9" rx="1" fill="none" stroke="#d0191f" stroke-width="1.2"/></svg>+61 (0)400 555 218</li>
      <li><svg viewBox="0 0 10 10"><path d="M1 3 Q5 0 9 3 L8 5 L6 4 L4 4 L2 5 Z M2 6 H8 V9 H2 Z" fill="#d0191f"/></svg>+61 (0)7 5550 1316</li>
      <li><svg viewBox="0 0 10 10"><path d="M2 1 L4 1 L5 3 L4 4 Q5 6 6 6 L7 5 L9 6 L9 8 Q5 9 2 5 Q1 3 2 1 Z" fill="#d0191f"/></svg>+61 (0)7 5550 1333</li>
      <li><svg viewBox="0 0 10 10"><rect x="1" y="3" width="8" height="5" fill="#d0191f"/><rect x="3" y="1" width="4" height="2" fill="#d0191f"/></svg>+61 (0)7 5550 1303</li>
      <li><svg viewBox="0 0 10 10"><rect x="0.6" y="2" width="8.8" height="6" fill="none" stroke="#d0191f" stroke-width="1.2"/><path d="M1 2.5 L5 5.5 L9 2.5" fill="none" stroke="#d0191f" stroke-width="1.2"/></svg>dwhitfield@korvalit.com.au</li>
      <li><svg viewBox="0 0 10 10"><circle cx="5" cy="5" r="4.3" fill="none" stroke="#d0191f" stroke-width="1.2"/><path d="M0.7 5 H9.3 M5 0.7 V9.3" stroke="#d0191f" stroke-width="1"/></svg>www.<span class="web-highlight">korvalit</span>.com.au</li>
    </ul>
    <div class="feature-block"></div>
  </section>

  <section class="card card-back" aria-label="Card back">
    <div class="brand">
      <span class="brand-square"></span>
      <span class="brand-name">korvalIT</span>
    </div>
  </section>
</main>
</body>
</html>
```